eCommerce Website Design for Children's Book Service

I am looking for a 5 page eCommerce website that includes a Shopping Cart. 'Lumiva Books' is the title of the company and its logo is attached. 'Sprouting wonder in words,' is the company's motto and 'spring green' is the main color. The website needs to appeal to families. Images of books and/or maple seeds (helicopter seeds) moving are part of the graphics.
Updates

I have updated my brief and I would like my website design to include 5 pages: home, about, products (books), blog, contact. WordPress is the web format that I am most comfortable with.

Target Market(s)

Families with young children

Coding

Coded - Design and coding required

Number of Pages Required

5+ page

Requirements
Must have
• Shopping cart page; contact page, books page with spaces of photos to go, blog page; spring green color
Nice to have
• A graphic that relates to motto : "sprouting wonder in words"
• WordPress

```html
<!DOCTYPE html>
<html lang="en">
<head>
<meta charset="utf-8">
<title>Lumiva Books – Sprouting wonder in words</title>
<link href="https://fonts.googleapis.com/css2?family=Playfair+Display:ital,wght@0,400;0,700;1,700&family=Lato:wght@400;700&display=swap" rel="stylesheet">
<style>
:root{
  --green:#3b8f2f;
  --green-dark:#2a6f22;
  --green-deep:#1f5a1a;
  --ink:#222;
  --muted:#555;
  --light:#f4f4f4;
  --line:#d9d9d9;
  --white:#fff;
  --teal:#8fd5d1;
  --pink:#f6b9c1;
}
*{box-sizing:border-box;margin:0;padding:0}
html,body{width:1200px;height:3982px;overflow:hidden}
body{position:relative;background:var(--white);font-family:"Lato",sans-serif;color:var(--ink)}
.serif{font-family:"Playfair Display",serif}
.abs{position:absolute}
.btn{position:absolute;display:flex;align-items:center;justify-content:center;background:var(--green);color:var(--white);font:700 13px "Lato",sans-serif;letter-spacing:.5px;text-transform:uppercase}

/* header */
.site-header{position:absolute;left:0;top:0;width:1200px;height:106px;background:var(--white)}
.brand{position:absolute;left:40px;top:-40px;width:210px;height:210px;border-radius:50%;background:var(--white);z-index:3;display:flex;flex-direction:column;align-items:center;justify-content:flex-end;padding-bottom:52px}
.brand-name{font:700 30px "Playfair Display",serif;color:var(--green)}
.brand-dot{width:22px;height:22px;background:var(--green);border-radius:50%;margin-bottom:6px}
.phone{left:415px;top:18px;font-size:15px;color:var(--green)}
.social-top{position:absolute;top:8px;width:30px;height:30px;border-radius:50%;background:var(--green)}
.signin{left:730px;top:18px;font-size:14px;color:var(--green)}
.search{position:absolute;left:791px;top:11px;width:165px;height:32px;border:1px solid #999;border-radius:3px;font-size:14px;color:#777;padding:6px 0 0 40px}
.search svg{position:absolute;left:12px;top:7px}
.get-started{left:966px;top:12px;width:157px;height:32px;border-radius:2px}
.main-nav{position:absolute;top:68px;font-size:14px;color:var(--green);letter-spacing:.5px}
.cart{position:absolute;left:1025px;top:60px;width:98px;height:32px;border:1px solid #999;border-radius:3px;font-size:13px;color:var(--ink);font-weight:700;padding:7px 0 0 12px}
.cart svg{position:absolute;right:12px;top:5px}

/* hero */
.hero{position:absolute;left:0;top:106px;width:1200px;height:539px;background:radial-gradient(ellipse at 35% 55%,#9aa37a 0%,#5f6b4a 40%,#2f3a2a 100%)}
.hero h1{position:absolute;left:0;width:1200px;top:232px;text-align:center;font:400 50px "Playfair Display",serif;color:var(--white)}
.hero p{position:absolute;left:0;width:1200px;top:306px;text-align:center;font-size:21px;color:var(--white)}
.hero .btn{left:544px;top:371px;width:112px;height:32px}

/* about */
.about{position:absolute;left:0;top:645px;width:1200px;height:417px;background:var(--light)}
.about h2{position:absolute;left:80px;top:90px;font:700 28px "Playfair Display",serif;color:var(--green)}
.about p{position:absolute;left:80px;top:150px;width:690px;font-size:15px;line-height:24px;color:#333}
.about .btn{left:80px;top:272px;width:116px;height:32px}
.card-shadow{position:absolute;left:860px;top:72px;width:240px;height:305px;background:#888}
.card-art{position:absolute;left:845px;top:58px;width:240px;height:305px;background:linear-gradient(160deg,#fff 30%,#e7ecf5 70%,#c9d7ee)}

/* feature grid */
.tile{position:absolute;width:300px;height:279px}
.tile-text{background:var(--white)}
.tile-text h3{position:absolute;left:21px;top:58px;font:700 22px "Playfair Display",serif;color:var(--green)}
.tile-text p{position:absolute;left:21px;top:96px;width:250px;font-size:15px;line-height:24px;color:var(--muted)}
.tile-text .btn{left:21px;top:190px;height:34px;padding:0 18px}

/* quote */
.quote{position:absolute;left:0;top:1620px;width:1200px;height:204px;background:var(--green)}
.quote blockquote{position:absolute;left:0;width:1200px;top:60px;text-align:center;font:700 23px "Playfair Display",serif;color:var(--white)}
.quote hr{position:absolute;left:585px;top:114px;width:30px;border:0;border-top:1px solid #cfe5c9}
.quote cite{position:absolute;left:0;width:1200px;top:128px;text-align:center;font-style:normal;font-size:14px;color:var(--white)}

/* books */
.section-title{position:absolute;left:0;width:1200px;text-align:center;font:700 28px "Playfair Display",serif;color:var(--green)}
.book{position:absolute;top:1925px;width:256px}
.book-cover{width:256px;height:332px}
.book h4{margin-top:38px;text-align:center;font:700 19px "Playfair Display",serif;color:var(--ink)}
.book span{display:block;margin-top:4px;text-align:center;font-size:14px;color:var(--muted)}

.partner{position:absolute;top:2510px;width:80px;height:80px}

/* mailing */
.mailing{position:absolute;left:0;top:2687px;width:1200px;height:295px;background:linear-gradient(100deg,#5d9a3e 0%,#2f7a24 40%,#236c1c 70%,#3c8a2c 100%)}
.mailing h2{position:absolute;right:77px;top:62px;font:700 28px "Playfair Display",serif;color:var(--white)}
.mailing p{position:absolute;right:77px;top:112px;font-size:14px;color:var(--white)}
.mailing .field{position:absolute;left:682px;top:148px;width:260px;height:48px;background:var(--white);font-size:14px;font-weight:700;color:#444;padding:15px 0 0 20px}
.mailing .signup{position:absolute;left:942px;top:148px;width:181px;height:48px;border:1px solid var(--white);color:var(--white);font-size:15px;font-weight:700;display:flex;align-items:center;justify-content:center}

/* blog */
.post{position:absolute;top:3112px;width:333px}
.post-img{width:333px;height:186px}
.post .tags{margin-top:34px;font-size:13px;color:var(--green)}
.post h4{margin-top:9px;font:700 19px "Playfair Display",serif;color:var(--ink)}
.post .byline{margin-top:5px;font-size:14px;color:#333}
.post p{margin-top:18px;font-size:14px;line-height:23px;color:#333}

/* footer */
.site-footer{position:absolute;left:0;top:3616px;width:1200px;height:366px;background:#f1f1f1}
.site-footer h5{position:absolute;top:42px;font:700 18px "Playfair Display",serif;color:var(--green)}
.input{position:absolute;height:42px;background:var(--white);border:1px solid #aaa;font-size:14px;color:#333;padding:12px 0 0 14px}
.foot-links{position:absolute;top:80px;font-size:15px;line-height:28px;color:#333;list-style:none}
.foot-social{position:absolute;top:88px;width:30px;height:30px;border-radius:50%;background:var(--green)}
.foot-rule{position:absolute;left:74px;width:1054px;border:0;border-top:1px solid #bbb}
.small{position:absolute;font-size:12px;color:#333}
.pay{position:absolute;top:3935px;width:42px;height:26px;border-radius:3px;background:var(--white);border:1px solid #ccc}
</style>
</head>
<body>

<header class="site-header">
  <div class="brand"><span class="brand-dot"></span><span class="brand-name">Lumiva Books</span></div>
  <span class="abs phone">1-800-555-0142</span>
  <span class="social-top" style="left:552px" aria-label="Social link"></span>
  <span class="social-top" style="left:596px" aria-label="Social link"></span>
  <span class="social-top" style="left:640px" aria-label="Social link"></span>
  <span class="social-top" style="left:684px" aria-label="Social link"></span>
  <span class="abs signin">Sign in</span>
  <div class="search"><svg width="16" height="16" viewBox="0 0 16 16"><circle cx="6.5" cy="6.5" r="5" fill="none" stroke="#333" stroke-width="2"/><line x1="10" y1="10" x2="15" y2="15" stroke="#333" stroke-width="2"/></svg>Search</div>
  <span class="btn get-started">Get Started</span>
  <nav>
    <span class="main-nav" style="left:582px">HOME</span>
    <span class="main-nav" style="left:660px">ABOUT</span>
    <span class="main-nav" style="left:742px">BOOKS</span>
    <span class="main-nav" style="left:829px">EVENTS</span>
    <span class="main-nav" style="left:920px">CONTACT</span>
  </nav>
  <div class="cart">CART
    <svg width="28" height="24" viewBox="0 0 28 24"><path d="M2 3h4l3 12h13l3-9H8" fill="none" stroke="#555" stroke-width="1.6"/><circle cx="11" cy="19" r="2" fill="#555"/><circle cx="20" cy="19" r="2" fill="#555"/><circle cx="23" cy="18" r="5" fill="var(--green)"/></svg>
  </div>
</header>

<section class="hero" role="img" aria-label="Photo of a young girl reading a yellow book on a park bench">
  <h1>Sprouting wonder in words</h1>
  <p>Suspendisse metus adipiscing. Cras fames dapibus. Vestibulum sit</p>
  <span class="btn">Shop Now</span>
</section>

<section class="about">
  <h2>About Me</h2>
  <p>Suspendisse metus adipiscing. Cras fames dapibus. Vestibulum sit consectetuer. Odio diam a sem praesentium et cursus arcu sapien. Maecenas amet eget ultrices morbi nibh vehicula vitae est curabitur risus wisi. Eget egestas aliquam. Est faucibus vehicula sed nec ullamcorper. Vulputate suspendisse lorem volutpat praesent voluptate lorem non neque amet elit condimentum.</p>
  <span class="btn">Read Blog</span>
  <div class="card-shadow"></div>
  <div class="card-art" role="img" aria-label="Illustrated greeting card reading Enjoy Today with a sleeping cat"></div>
</section>

<section>
  <div class="tile tile-text" style="left:0;top:1062px"><h3>Neque porro quisquam</h3><p>Lorem Ipsum is simply dummy text of the printing and typesetting industry.</p><span class="btn">View Collection</span></div>
  <div class="tile" style="left:300px;top:1062px;background:linear-gradient(135deg,#8a4a2a,#c7744a 45%,#3f6b8f)" role="img" aria-label="Photo of a girl choosing a book from library shelves"></div>
  <div class="tile tile-text" style="left:600px;top:1062px"><h3>Neque porro quisquam</h3><p>Lorem Ipsum is simply dummy text of the printing and typesetting industry.</p><span class="btn">Shop Now</span></div>
  <div class="tile" style="left:900px;top:1062px;background:#ececec"><div class="abs" style="left:70px;top:20px;width:160px;height:230px;background:linear-gradient(160deg,#fff 40%,#e6f0e2)" role="img" aria-label="Illustrated birthday card reading Welcome to my birthday"></div></div>

  <div class="tile" style="left:0;top:1341px;background:linear-gradient(120deg,#d9d2c8,#b98a66 50%,#e1b45a)" role="img" aria-label="Photo of a girl lying on the floor reading a book"></div>
  <div class="tile tile-text" style="left:300px;top:1341px"><h3>Neque porro quisquam</h3><p>Lorem Ipsum is simply dummy text of the printing and typesetting industry.</p><span class="btn">Read Blog</span></div>
  <div class="tile" style="left:600px;top:1341px;background:linear-gradient(120deg,#c9c2b5,#7a5a44 50%,#b7a99a)" role="img" aria-label="Photo of a mother reading to her child"></div>
  <div class="tile tile-text" style="left:900px;top:1341px"><h3>Neque porro quisquam</h3><p>Lorem Ipsum is simply dummy text of the printing and typesetting industry.</p><span class="btn">Read More</span></div>
</section>

<section class="quote">
  <blockquote>“Sed ut perspiciatis unde omnis iste natus error sit voluptatem accusantium”</blockquote>
  <hr>
  <cite>Japanese Proverb</cite>
</section>

<section>
  <h2 class="section-title" style="top:1854px">Our Books</h2>
  <div class="book" style="left:61px"><div class="book-cover" style="background:var(--teal)" role="img" aria-label="Book cover illustration of a child astronaut"></div><h4>BOOK 1</h4><span>from $33.00</span></div>
  <div class="book" style="left:335px"><div class="book-cover" style="background:var(--pink)" role="img" aria-label="Book cover illustration of a child in a rocket"></div><h4>BOOK 2</h4><span>from $33.00</span></div>
  <div class="book" style="left:608px"><div class="book-cover" style="background:var(--teal)" role="img" aria-label="Book cover illustration of an astronaut and a friendly alien"></div><h4>BOOK 3</h4><span>from $33.00</span></div>
  <div class="book" style="left:881px"><div class="book-cover" style="background:linear-gradient(#fff 0 30%,var(--pink) 30%)" role="img" aria-label="Book cover illustration of a friendly sea monster"></div><h4>BOOK 4</h4><span>from $33.00</span></div>

  <h2 class="section-title" style="top:2402px">Our partnerships and certifications</h2>
  <span class="partner" style="left:218px;border:2px solid #999;border-radius:50%" aria-label="Partner badge"></span>
  <span class="partner" style="left:387px;background:#aaa;border-radius:50%" aria-label="Partner badge"></span>
  <span class="partner" style="left:555px;top:2515px;width:80px;height:70px;background:#999;border-radius:6px" aria-label="Partner badge"></span>
  <span class="partner" style="left:705px;top:2535px;width:120px;height:30px;background:#999;border-radius:4px" aria-label="Partner badge"></span>
  <span class="partner" style="left:895px;border:3px solid #aaa;border-radius:50%" aria-label="Partner badge"></span>
</section>

<section class="mailing" role="img" aria-label="Green-tinted photo of a child reading">
  <h2>Join our mailing list!</h2>
  <p>Sign up to get the latest on sales, new releases and more…</p>
  <div class="field">EMAIL ADDRESS</div>
  <div class="signup">SIGN UP</div>
</section>

<section>
  <h2 class="section-title" style="top:3028px">Our Blog</h2>
  <article class="post" style="left:74px"><div class="post-img" style="background:linear-gradient(120deg,#e4ddd0,#b88a5c 50%,#d9c9a8)" role="img" aria-label="Photo of a girl sitting among stacks of books"></div><div class="tags">Book , Kids book , Story</div><h4>Sed ut perspiciatis unde omnis</h4><div class="byline">by Nora Whitfield December 16, 2019</div><p>Sed ut perspiciatis unde omnis iste natus error sit voluptatem accusantium doloremque laudantium, totam rem aperiam, eaque ipsa quae ab illo inventore veritatis</p></article>
  <article class="post" style="left:433px"><div class="post-img" style="background:linear-gradient(120deg,#6b3a22,#c26a3a 45%,#2f5d86)" role="img" aria-label="Photo of colourful library bookshelves"></div><div class="tags">Book , Kids book , Story</div><h4>Sed ut perspiciatis unde omnis</h4><div class="byline">by Nora Whitfield December 16, 2019</div><p>Sed ut perspiciatis unde omnis iste natus error sit voluptatem accusantium doloremque laudantium, totam rem aperiam, eaque ipsa quae ab illo inventore veritatis</p></article>
  <article class="post" style="left:794px"><div class="post-img" style="background:linear-gradient(120deg,#d8dde0,#4f7fb4 50%,#d9b89a)" role="img" aria-label="Photo of a father and son reading together"></div><div class="tags">Book , Kids book , Story</div><h4>Sed ut perspiciatis unde omnis</h4><div class="byline">by Nora Whitfield December 16, 2019</div><p>Sed ut perspiciatis unde omnis iste natus error sit voluptatem accusantium doloremque laudantium, totam rem aperiam, eaque ipsa quae ab illo inventore veritatis</p></article>
</section>

<footer class="site-footer">
  <h5 style="left:74px">Sign up for our Newsletter</h5>
  <div class="input" style="left:74px;top:80px;width:197px">First name</div>
  <div class="input" style="left:282px;top:80px;width:193px">Last name</div>
  <div class="input" style="left:74px;top:135px;width:270px">Email Address</div>
  <span class="btn" style="left:356px;top:135px;width:119px;height:42px;font-size:14px">Sign Up</span>

  <h5 style="left:499px">Company</h5>
  <ul class="foot-links" style="left:499px"><li>About Us</li><li>Books</li><li>Terms and Policies</li><li>FAQs</li></ul>
  <h5 style="left:722px">Communities</h5>
  <ul class="foot-links" style="left:722px"><li>Events</li><li>Our Blog</li><li>Contact Us</li></ul>
  <h5 style="left:964px">Social</h5>
  <span class="foot-social" style="left:962px" aria-label="Social link"></span>
  <span class="foot-social" style="left:1003px" aria-label="Social link"></span>
  <span class="foot-social" style="left:1044px" aria-label="Social link"></span>
  <span class="foot-social" style="left:1085px" aria-label="Social link"></span>

  <hr class="foot-rule" style="top:211px">
  <span class="small" style="left:74px;top:228px">Ut enim ad minima veniam, quis nostrum exercitationem ullam corporis</span>
  <hr class="foot-rule" style="top:258px">
  <span class="small" style="left:74px;top:288px">© 2019 | www.lumivabooks.com</span>
  <span class="small" style="left:880px;top:282px">Quis nostrum exercitationem ullam corporis</span>
</footer>
<span class="pay" style="left:828px" aria-label="Payment method"></span>
<span class="pay" style="left:874px" aria-label="Payment method"></span>
<span class="pay" style="left:920px" aria-label="Payment method"></span>
<span class="pay" style="left:966px" aria-label="Payment method"></span>
<span class="pay" style="left:1012px" aria-label="Payment method"></span>
<span class="pay" style="left:1058px" aria-label="Payment method"></span>

</body>
</html>
```